Australian Trucking Company Requires Professional Looking Stationary

We require a professional looking stationary design that incorporates our newly designed logo.

Our business, called "Brell Haulage Contracting", provides contracting work, transport and logistics to business in Western Australia particularly with links to the mining sector.

We are a small business looking to expand and our new logo and our new stationary will help develop our brand image in our market place.

Target Market(s)

Businesses and Corporation with links to the Mining Sector

Industry/Entity Type

Small Business

Requirements
Must have
• The letterhead must have the following details:
The new logo

Text saying: "Brell Holdings Pty Ltd (ACN 582 316 907) ATF The Brell Discretionary Trust T/AS"
"ABN 71 834 209 553"
Address "P.O Box 817 Wattlegrove WA, 6958"
Phone: 08 9352 7140
Email: brellhaul@mailbox-example.com.au

The text on the letterhead should be editable as the details are likely to change in the near future. Provision should be made for a website address all though one isn't available at the moment.

The styling, layout and font text is entirely up to the designer.

```html
<!DOCTYPE html>
<html lang="en">
<head>
<meta charset="utf-8">
<title>Brell Haulage Contracting – Business Card</title>
<link rel="stylesheet" href="https://fonts.googleapis.com/css2?family=Open+Sans:wght@400;600;700&display=swap">
<style>
  :root {
    --backdrop: #ecebe8;
    --card: #ffffff;
    --brand-red: #d7192a;
    --brand-dark-red: #9e1420;
    --ink: #3a3a3a;
    --ink-soft: #555555;
    --mark-grey: #5a5a5a;
    --card-shadow: rgba(0, 0, 0, 0.18);
  }
  * { box-sizing: border-box; margin: 0; padding: 0; }
  html, body {
    width: 1200px;
    height: 650px;
    overflow: hidden;
    background: var(--backdrop);
    font-family: "Open Sans", Arial, sans-serif;
  }
  .stage {
    position: relative;
    width: 1200px;
    height: 650px;
    display: flex;
    align-items: center;
    justify-content: center;
    gap: 60px;
  }
  .card {
    position: relative;
    width: 520px;
    height: 300px;
    background: var(--card);
    border-radius: 26px;
    box-shadow: 0 6px 18px var(--card-shadow);
    overflow: hidden;
  }

  /* Front */
  .brand {
    position: absolute;
    top: 42px;
    left: 40px;
    display: flex;
    align-items: center;
    gap: 14px;
  }
  .brand-square {
    width: 34px;
    height: 34px;
    background: var(--brand-dark-red);
  }
  .brand-name {
    font-weight: 700;
    font-size: 26px;
    line-height: 1.05;
    color: var(--brand-dark-red);
    text-transform: uppercase;
    letter-spacing: 0.5px;
  }
  .holder {
    position: absolute;
    top: 150px;
    left: 40px;
    font-size: 19px;
    color: var(--ink);
  }
  .holder-name {
    font-weight: 700;
    color: var(--brand-red);
  }
  .contact-list {
    position: absolute;
    top: 188px;
    left: 40px;
    list-style: none;
    font-size: 13px;
    color: var(--ink-soft);
  }
  .contact-list li {
    display: flex;
    align-items: center;
    gap: 7px;
    height: 19px;
  }
  .contact-list li.address { margin-top: 8px; }
  .contact-icon { width: 11px; height: 11px; fill: var(--ink); flex: none; }

  /* Back */
  .card-back {
    display: flex;
    flex-direction: column;
    align-items: center;
    justify-content: center;
  }
  .back-brand {
    display: flex;
    align-items: center;
    gap: 16px;
    margin-top: -10px;
  }
  .back-circle {
    width: 44px;
    height: 44px;
    border-radius: 50%;
    background: var(--mark-grey);
  }
  .back-name {
    font-weight: 700;
    font-size: 28px;
    line-height: 1.1;
    color: var(--mark-grey);
    text-transform: uppercase;
  }
  .back-web {
    margin-top: 48px;
    font-size: 22px;
    letter-spacing: 1.5px;
    color: var(--ink);
  }
</style>
</head>
<body>
<main class="stage">
  <section class="card card-front" aria-label="Business card front">
    <div class="brand">
      <span class="brand-square" aria-hidden="true"></span>
      <span class="brand-name">Brell Haulage<br>Contracting</span>
    </div>
    <p class="holder"><span class="holder-name">Your Name,</span> Title</p>
    <ul class="contact-list">
      <li>
        <svg class="contact-icon" viewBox="0 0 24 24" aria-hidden="true"><path d="M6.6 10.8a15.1 15.1 0 0 0 6.6 6.6l2.2-2.2a1 1 0 0 1 1-.25 11.4 11.4 0 0 0 3.6.57 1 1 0 0 1 1 1V20a1 1 0 0 1-1 1A17 17 0 0 1 3 4a1 1 0 0 1 1-1h3.5a1 1 0 0 1 1 1c0 1.25.2 2.45.57 3.57a1 1 0 0 1-.25 1z"/></svg>
        08 9352 7140
      </li>
      <li>
        <svg class="contact-icon" viewBox="0 0 24 24" aria-hidden="true"><path d="M2 5h20v14H2z M2 5l10 8 10-8" /></svg>
        brellhaul@mailbox-example.com.au
      </li>
      <li>
        <svg class="contact-icon" viewBox="0 0 24 24" aria-hidden="true"><circle cx="12" cy="12" r="10"/><path d="M2 12h20M12 2c3 3 3 17 0 20M12 2c-3 3-3 17 0 20" stroke="#fff" stroke-width="1.6" fill="none"/></svg>
        www.brellhaul-example.com.au
      </li>
      <li class="address">
        <svg class="contact-icon" viewBox="0 0 24 24" aria-hidden="true"><path d="M12 3l10 9h-3v9h-5v-6h-4v6H5v-9H2z"/></svg>
        P.O Box 817 Wattlegrove WA, 6958
      </li>
    </ul>
  </section>

  <section class="card card-back" aria-label="Business card back">
    <div class="back-brand">
      <span class="back-circle" aria-hidden="true"></span>
      <span class="back-name">Brell Haulage<br>Contracting</span>
    </div>
    <p class="back-web">www.brellhaul-example.com.au</p>
  </section>
</main>
</body>
</html>
```